Dentistry Office

We want a new design for a Dentist's office website.

The theme is: "We provide high quality, state-of-the-art, dental care in a comfortable, caring environment."

The site currently has a menu on the left of the page with about 40 items on it. There is a great deal of textual content on each page, plus several illustrations.

We want to do this using CSS, so we need specifications in the CSS for all possible elements. The CSS needs to be named in a logical manner for easy use.

Every dentist on the planet seems to use lots of Flash. We don't want to because it is so distracting. We are looking for an elegant solution targeting 24-55 age group, but not excluding anyone.

The following (from another dentist's site) can give you a taste of what we want to communicate on the site:

"After 20 years of teaching dentists how to refine their technique and many years of writing textbooks, I currently devote my time to my office and the hands-on practice of dentistry. I'd like to welcome you personally to my dental practice, and I invite you to meet my highly experienced team of professionals.

"We have offered complete dental care of the highest quality since 1978. We provide Preventive Services, Tooth Whitening and Cosmetic Dentistry for a beautiful smile, Endodontics (root canal treatment) to treat painful teeth, Sedation Dentistry so you can relax, and Dental Implants to restore what is missing. We offer total care.

"Our approach to your health is simple: We use our education, experience and dedication to provide every patient with superior dental care.

"This passion for excellence is not just a goal, but a standard every member of our team holds.

"We also pride ourselves with our state of the art procedures, training and technology. This includes creating a beautiful smile using techniques that preserve as much of the original tooth as possible.

"Our abilities are renowned throughout the dental profession and I hope if you have any questions you will contact us by an e-mail note, by phone or just by dropping by."

Keep in mind the screen shape and dimensions. Your design needs to work in the normal screen proportions, regardless of how it looks when you post it here. Scrolling is OK, but the first impression needs to work.
Updates

Keep in mind that there will be about 250 words, or more, on each page.

Competitors web sites:

http://www.brindlecovedentist.example/

http://www.brindlecovedentalcare.example/

http://www.grinsbymarlowvaledental.example/

http://www.tenbyfamilydentalcare.example/

http://www.quelmardental.example/

http://www.dovrinadental.example/

We need to compete with these.

Target Market(s)

Generally adults seeking the most experienced and comfortable-to-be-with dentist.

Industry/Entity Type

Training

Requirements
Must have
• Must stand apart from other dentists.
• Must be elegant.
• Must have a horizontal menu structure across all columns, NOT a vertical that requires scrolling, no popout, pop down, etc. menus.
• We are looking for something special.
• Do not waste your time or ours putting up templates and things you have used before.
• Personally, I do not see how someone outside the US can understand the northern California dental market. But you are welcome to try.
Should not have
• Flash or graphics that move
• The look of a template
• Folksy fonts
• Looks like you used it 20 times before

```html
<!DOCTYPE html>
<html lang="en">
<head>
<meta charset="utf-8">
<title>Conrad Pellow, DDS, FAGD — Brindle Cove Dentist</title>
<link rel="stylesheet" href="https://fonts.googleapis.com/css2?family=Arimo:wght@400;700&family=Tinos:wght@400;700&display=swap">
<style>
:root{
  --page-top:#f1f2f3;
  --page-bottom:#4d5d69;
  --white:#ffffff;
  --ink:#2b2b2b;
  --ink-soft:#444a4f;
  --nav-dark:#1d1f21;
  --nav-mid:#3a3d40;
  --panel-dark:#2a2c2e;
  --panel-line:#55595d;
  --panel-text:#cfd3d6;
  --hero-frame:#2c3135;
  --hero-teal:#5f7e89;
  --hero-light:#dfe7ea;
  --box-line:#9aa3a8;
  --footer-text:#eef1f3;
  --serif:"Tinos", "Times New Roman", serif;
  --sans:"Arimo", Arial, sans-serif;
}
*{box-sizing:border-box;margin:0;padding:0}
html,body{width:852px;height:1200px;overflow:hidden}
body{
  position:relative;
  font-family:var(--sans);
  color:var(--ink);
  background:linear-gradient(180deg,var(--page-top) 0,#d7dadc 560px,#8a969e 900px,var(--page-bottom) 1200px);
}
.site{position:absolute;left:89px;top:7px;width:673px}

/* header */
.site-header{height:60px;background:linear-gradient(#ffffff,#eceeef);position:relative;border:1px solid #d5d8da}
.brand{position:absolute;left:16px;top:13px;font-family:var(--serif);font-size:22px;color:#2a2a2a;line-height:1;white-space:nowrap}
.brand small{font-size:19px;color:#555}
.brand-sub{position:absolute;left:145px;top:39px;font-family:var(--serif);font-size:11.5px;color:#333;white-space:nowrap}
.header-contact{position:absolute;right:10px;top:8px;font-family:var(--serif);font-size:9.5px;line-height:11.5px;color:#222;font-style:normal;white-space:nowrap}

/* navigation */
.main-nav{margin-top:5px;height:29px;background:linear-gradient(var(--nav-mid),var(--nav-dark));display:flex;align-items:center;justify-content:space-between;padding:0 12px 0 20px;border-top:1px solid #5a5e62}
.main-nav a{color:#fff;text-decoration:none;font-family:var(--serif);font-size:11px;font-weight:700;white-space:nowrap}
.main-nav .sep{color:#bbb;font-size:11px}

/* hero */
.hero{margin-top:5px;height:190px;background:var(--hero-frame);padding:4px;position:relative}
.hero-inner{height:100%;background:linear-gradient(100deg,#4b6570 0,var(--hero-teal) 30%,#a9bdc4 62%,var(--hero-light) 100%);position:relative;overflow:hidden}
.hero-photo{position:absolute;right:0;top:0;width:240px;height:100%;background:linear-gradient(90deg,rgba(223,231,234,0),#eef1f2 35%,#e9dcd2 70%,#f2e6df)}
.hero-quote{position:absolute;left:32px;top:50px;font-family:var(--serif);font-size:16.5px;line-height:20px;color:#fff;width:330px}
.quote-mark{position:absolute;font-family:var(--serif);font-size:26px;color:rgba(255,255,255,.55)}

/* service menu */
.service-menu{margin-top:10px;height:155px;background:var(--panel-dark);display:flex;padding:6px 8px 0 14px}
.service-col{width:124px;padding-right:10px}
.service-col:nth-child(2),.service-col:nth-child(3){width:138px}
.service-col:nth-child(4){width:128px}
.service-col h3{font-family:var(--serif);font-weight:400;font-size:12.5px;color:#fff;border-bottom:1px solid var(--panel-line);padding-bottom:2px;margin-bottom:3px;white-space:nowrap}
.service-col li{list-style:none;font-size:8.7px;line-height:12px;color:var(--panel-text);white-space:nowrap}
.service-col li::before{content:"» ";color:#9aa0a4}

/* content */
.content{background:var(--white);height:614px;position:relative;padding:14px 0 0 18px}
.main-col{width:460px;font-size:8.8px;line-height:11.2px;color:var(--ink-soft)}
.main-col h1{font-family:var(--serif);font-weight:400;font-size:17px;color:#222;margin-bottom:8px}
.main-col h2{font-family:var(--serif);font-weight:400;font-size:13px;color:#222;margin:10px 0 6px}
.main-col p{margin-bottom:8px}
.provides li{list-style:none;padding-left:9px;position:relative;margin-bottom:6px}
.provides li::before{content:"•";position:absolute;left:0}
.main-col .lead{font-family:var(--serif);font-size:13.5px;line-height:16px;color:#222;margin:6px 0 12px}
.signature{font-family:var(--serif);font-size:13px;color:#222}

.side-col{position:absolute;left:486px;top:14px;width:164px}
.office-photo{height:120px;border-radius:8px;border:1px solid var(--box-line);background:linear-gradient(160deg,#b9c6b1,#6e6b5b 45%,#8d7c6a 70%,#9ba68e)}
.side-box{border:1px solid var(--box-line);border-radius:10px;background:#fff;margin-top:26px;padding:6px 8px;box-shadow:0 1px 3px rgba(0,0,0,.12)}
.side-box h4{font-family:var(--serif);font-weight:400;font-size:13px;text-align:center;color:#222;margin-bottom:6px}
.map-area{height:200px;background:linear-gradient(#f4f6f7,#e4e8ea);border:1px solid #d2d7da}
.map-link{display:block;text-align:center;font-size:8.5px;color:#222;margin-top:5px;text-decoration:underline}
.hours{margin-top:8px}
.hours p{font-size:9px;color:#222;margin-bottom:3px}
.hours li{list-style:none;font-size:9px;line-height:11.6px;font-style:italic;font-weight:700;color:#111;white-space:nowrap}
.hours li::before{content:"› "}

/* footer */
.site-footer{position:absolute;left:89px;top:1078px;width:673px;height:90px}
.footer-info{position:absolute;left:0;top:18px;font-size:8.3px;line-height:10.5px;color:var(--footer-text);font-weight:700}
.footer-info .gap{height:10px}
.partner-box{position:absolute;left:348px;top:6px;width:325px;height:82px;background:#fff;border-radius:9px;padding:4px 8px 5px}
.partner-box .label{font-size:8px;line-height:10px;color:#333}
.partners{display:flex;gap:10px;margin-top:3px}
.partner{width:94px}
.partner .badge{width:62px;height:16px;background:#c7ced2;border-radius:2px;margin-bottom:3px}
.partner li{list-style:none;font-size:6.8px;line-height:8px;color:#222;white-space:nowrap}
</style>
</head>
<body>
<div class="site">
  <header class="site-header">
    <div class="brand">Conrad Pellow, <small>DDS, FAGD</small></div>
    <div class="brand-sub">Brindle Cove Dentist</div>
    <address class="header-contact">Conrad Pellow, DDS, FAGD<br>2240 Larchmere Rd. Ste B<br>Brindle Cove, CA 90210<br>555-010-4412</address>
  </header>

  <nav class="main-nav">
    <a href="#">Home</a><span class="sep">|</span>
    <a href="#">Why We Are Different?</a><span class="sep">|</span>
    <a href="#">Technologies We Offer</a><span class="sep">|</span>
    <a href="#">Meet Dr. Pellow</a><span class="sep">|</span>
    <a href="#">Our Staff</a><span class="sep">|</span>
    <a href="#">Contact Us / Links</a>
  </nav>

  <section class="hero">
    <div class="hero-inner">
      <div class="hero-photo" role="img" aria-label="Photo of a smiling woman holding a pink gerbera daisy"></div>
      <span class="quote-mark" style="left:22px;top:22px">“</span>
      <p class="hero-quote">Brindle Cove Dentist - Conrad Pellow, DDS, Providing Cosmetic Dentistry Excellence to Patients in Brindle Cove, Marrow County and the Greywater Bay Area.</p>
      <span class="quote-mark" style="left:330px;top:130px">”</span>
    </div>
  </section>

  <section class="service-menu">
    <div class="service-col"><h3>Education</h3><ul>
      <li>Emergency Dental Care</li><li>Your Mouth</li><li>Your Tooth</li><li>Cracked Tooth?</li><li>Missing a Tooth?</li><li>Sensitive Teeth</li><li>Dry Mouth</li><li>Tooth Grinding</li><li>Sleep Dentistry</li><li>Videos</li></ul></div>
    <div class="service-col"><h3>Preventative</h3><ul>
      <li>What is Preventive Care?</li><li>Taking Care of Your Teeth</li><li>Eating Right</li><li>Dental Check-Ups</li><li>Sealants</li><li>Periodontal Disease</li><li>Kicking the Habit</li><li>Night Guards</li><li>Dental X-Rays</li><li>Antibiotics with Treatment</li></ul></div>
    <div class="service-col"><h3>Cosmetics</h3><ul>
      <li>Cosmetic Dentistry</li><li>Bleaching and Whitening</li><li>Cosmetic Bonding</li><li>Esthetic Veneers</li><li>Tooth Shaping</li></ul></div>
    <div class="service-col"><h3>Restorations</h3><ul>
      <li>Crowns/Caps: Each Step</li><li>CMBRs</li><li>Porcelain Bridges</li><li>Bonded Dental Bridges</li><li>Gold Restorations</li><li>Implants</li><li>Treating Cracked Teeth</li><li>Periodontal (gum) Treatment</li></ul></div>
    <div class="service-col"><h3>Visiting our office</h3><ul>
      <li>Where to Stay</li><li>First Visit / Map</li><li>Financial Policy</li><li>Dental Insurance</li></ul></div>
  </section>

  <main class="content">
    <div class="main-col">
      <h1>Welcome to Our Website</h1>
      <p>In Brindle Cove, when you're a patient of Dr. Pellow, you can be confident that you're receiving care from the most experienced, knowledgeable, and skilled cosmetic dentist in Marrow County.</p>
      <p>Dr. Pellow is an award-winning leader in restorative dentistry and a genial professional. His humor, dedication, and talent ensure you a pleasant experience and superb, long-lasting results.</p>
      <h2>Dr. Pellow Provides</h2>
      <ul class="provides">
        <li>General dentistry—oral hygiene, cavity detection and repair, crowns.</li>
        <li>Cosmetic/restorative dentistry—broken or misshapen teeth, crooked smiles, unsightly gaps</li>
        <li>Non-metal fillings—nontoxic, durable tooth-colored resin fillings that are proven to provide better results</li>
        <li>Tooth shaping—extending, shortening or otherwise reshaping teeth for improved esthetics</li>
        <li>Complete smile make-over's—resin veneers that reshape the whole mouth while preserving natural teeth</li>
        <li>Tooth whitening—at-home bleaching options to make teeth appear years younger</li>
        <li>Laser Dentistry, Sleep Dentistry, and Implant Dentistry with the Finest and Latest Equipment and Materials.</li>
        <li>Dental Implants to replace missing teeth.</li>
        <li>Sedation Dentistry so you can be relaxed.</li>
      </ul>
      <h2>Dr. Pellow’s Commitment</h2>
      <p>After 25 years of teaching dentists how to refine their technique and many years of writing textbooks, I currently devote my time to my office and the hands-on practice of dentistry. I'd like to welcome you personally to my dental practice, and I invite you to meet my highly experienced team of professionals.</p>
      <p>Dr. Pellow and his Associated have offered complete dental care of the highest quality since 1978. We provide Preventive Services, Tooth Whitening and Cosmetic Dentistry for a beautiful smile, Endodontics (root canal treatment) to treat painful teeth, Sedation Dentistry so you can relax, and Dental Implants to restore what is missing. We offer total care.</p>
      <p class="lead">Our approach to your health is simple: We use our education, experience and dedication to provide every patient with superior dental care.</p>
      <p class="lead">This passion for excellence is not just a goal, but a standard every member of our team holds.</p>
      <p>We also pride ourselves with our state of the art procedures, training and technology. This includes creating a beautiful smile using techniques that preserve as much of the original tooth as possible.</p>
      <p>Our abilities are renowned throughout the dental profession and I hope if you have any questions you will contact us by an e-mail note, by phone or just by dropping by.</p>
      <p>Thank you.</p>
      <p>Sincerely,</p>
      <p class="signature">Conrad Pellow, DDS FAGD</p>
    </div>

    <aside class="side-col">
      <div class="office-photo" role="img" aria-label="Photo of the dental office building among trees"></div>
      <div class="side-box">
        <h4>Brindle Cove Map:</h4>
        <div class="map-area" role="img" aria-label="Street map showing directions to the office"></div>
        <a class="map-link" href="#">Click for Large View</a>
      </div>
      <div class="side-box" style="margin-top:8px">
        <h4>Office Timing</h4>
        <div class="hours">
          <p>Our usual office hours are:</p>
          <ul>
            <li>Monday 9 am to 6 pm</li>
            <li>Tuesday 9 am to 5 pm</li>
            <li>Wednesday 9 am to 5 pm</li>
            <li>Thursday 9 am to 5 pm</li>
            <li>Friday 7:30 am to 5 pm</li>
          </ul>
        </div>
      </div>
    </aside>
  </main>
</div>

<footer class="site-footer">
  <div class="footer-info">
    Copyright © 2010 pellowdental.example. All Rights Reserved.
    <div class="gap"></div>
    Office Phone: (555) 010-4412<br>
    Office Fax: (555) 010-4433<br>
    email Dr. Pellow at: office@pellowdental.example
  </div>
  <div class="partner-box">
    <div class="label">Dental Links:</div>
    <div class="partners">
      <div class="partner"><div class="badge"></div><ul>
        <li>Emergency Dental Help</li><li>Oral Health Videos</li><li>Oral Health Topics</li><li>Dental Minute News</li></ul></div>
      <div class="partner"><div class="badge"></div><ul>
        <li>Dental Emergencies</li><li>Dental Health</li><li>Dental Insurance</li><li>Kids Corner</li><li>Dental Terminology</li></ul></div>
      <div class="partner"><div class="badge"></div><ul>
        <li>Course Outlines</li><li>Upcoming Courses</li><li>Web Links</li><li>Dr. Pellow CV</li><li>Academy Store</li></ul></div>
    </div>
  </div>
</footer>
</body>
</html>
```